Health Care Company with Logo Needs Business Cards designed

We are a luxury behavioral health company looking for business cards design we already have a logo and are looking for someone to design a sophisticated luxurious looking business card. Please note that Card design should be captivating just like the logo and also encompass the logo color

Industry/Entity Type

Healthcare

Contact Information for Business Card

Logo,company name, tagline, my name and title, contact details, and physical address

```html
<!DOCTYPE html>
<html lang="en">
<head>
<meta charset="utf-8">
<title>Larkvale Behavioral Health – Business Card</title>
<link href="https://fonts.googleapis.com/css2?family=Arimo:wght@400;700&family=Roboto+Condensed:wght@700&display=swap" rel="stylesheet">
<style>
  :root {
    --page-bg: #d8d2c8;
    --card-light: #f1e9da;
    --card-mist: #e4e6e8;
    --card-warm: #cbbba2;
    --purple: #5b2a7a;
    --teal: #147ea0;
    --blue: #0a6bb5;
    --sky: #1b8fcf;
    --ink: #2b2b2b;
  }
  html, body {
    margin: 0;
    width: 1200px;
    height: 927px;
    overflow: hidden;
    background: var(--page-bg);
  }
  .card {
    position: absolute;
    left: 50px;
    top: 156px;
    width: 1100px;
    height: 614px;
    background: linear-gradient(100deg, var(--card-light) 0%, var(--card-mist) 38%, #ddd3c2 62%, var(--card-warm) 100%);
    box-shadow: 0 10px 30px rgba(0,0,0,0.18);
    overflow: hidden;
    font-family: "Arimo", Arial, sans-serif;
  }
  .holder {
    position: absolute;
    right: 66px;
    top: 62px;
    text-align: right;
  }
  .holder-name {
    margin: 0;
    font-weight: 700;
    font-size: 36px;
    line-height: 1.1;
    color: var(--teal);
  }
  .holder-title {
    margin: 2px 0 0;
    font-size: 28px;
    color: var(--ink);
  }
  .accent-bar {
    position: absolute;
    right: 0;
    top: 68px;
    width: 19px;
    height: 74px;
    background: var(--blue);
  }
  .brand-square {
    position: absolute;
    left: 89px;
    top: 240px;
    width: 92px;
    height: 92px;
    background: var(--purple);
  }
  .brand-name {
    position: absolute;
    left: 224px;
    top: 238px;
    margin: 0;
    font-family: "Roboto Condensed", "Arial Narrow", sans-serif;
    font-weight: 700;
    font-size: 51px;
    line-height: 1;
    color: var(--purple);
    white-space: nowrap;
  }
  .brand-tagline {
    position: absolute;
    left: 225px;
    top: 300px;
    margin: 0;
    font-family: "Roboto Condensed", "Arial Narrow", sans-serif;
    font-weight: 700;
    font-size: 15px;
    letter-spacing: 0.4em;
    color: var(--sky);
    white-space: nowrap;
  }
  .contact-list {
    position: absolute;
    left: 228px;
    top: 374px;
    margin: 0;
    padding: 0;
    list-style: none;
  }
  .contact-item {
    display: flex;
    align-items: center;
    height: 38px;
    font-size: 30px;
    color: var(--ink);
  }
  .contact-icon {
    width: 24px;
    height: 24px;
    margin-right: 19px;
    flex: none;
  }
  .divider {
    position: absolute;
    left: 228px;
    top: 500px;
    width: 454px;
    height: 2px;
    background: #3a3a3a;
  }
  .address {
    position: absolute;
    left: 228px;
    top: 507px;
    margin: 0;
    font-size: 30px;
    color: var(--ink);
  }
</style>
</head>
<body>
  <article class="card">
    <div class="accent-bar"></div>
    <header class="holder">
      <p class="holder-name">Daniel Hart</p>
      <p class="holder-title">Manager</p>
    </header>

    <div class="brand-square"></div>
    <h1 class="brand-name">Larkvale Behavioral Health</h1>
    <p class="brand-tagline">COMMITTED TO CALM, CARING AND RENEWAL</p>

    <ul class="contact-list">
      <li class="contact-item">
        <svg class="contact-icon" viewBox="0 0 24 24" aria-hidden="true">
          <path fill="#0a6bb5" d="M6.6 10.8a15.1 15.1 0 0 0 6.6 6.6l2.2-2.2c.3-.3.7-.4 1-.2 1.1.4 2.3.6 3.6.6.6 0 1 .4 1 1V20c0 .6-.4 1-1 1A17 17 0 0 1 3 4c0-.6.4-1 1-1h3.5c.6 0 1 .4 1 1 0 1.3.2 2.5.6 3.6.1.3 0 .7-.2 1z"/>
        </svg>
        <span>123-456-2100</span>
      </li>
      <li class="contact-item">
        <svg class="contact-icon" viewBox="0 0 24 24" aria-hidden="true">
          <rect x="2.5" y="5" width="19" height="14" rx="1.5" fill="none" stroke="#0a6bb5" stroke-width="2"/>
          <path d="M3 6l9 7 9-7" fill="none" stroke="#0a6bb5" stroke-width="2"/>
        </svg>
        <span>youremail@gmail.com</span>
      </li>
      <li class="contact-item">
        <svg class="contact-icon" viewBox="0 0 24 24" aria-hidden="true">
          <g fill="none" stroke="#0a6bb5" stroke-width="1.8">
            <circle cx="12" cy="12" r="9.5"/>
            <ellipse cx="12" cy="12" rx="4.2" ry="9.5"/>
            <path d="M2.5 12h19M4 7h16M4 17h16"/>
          </g>
        </svg>
        <span>www.yourwebsite.com</span>
      </li>
    </ul>

    <div class="divider"></div>
    <p class="address">Your address, city, state, ZIP 0000</p>
  </article>
</body>
</html>
```